Redesign of business card for Cedar Ridge Mechanical

We are looking for a new design for our business cards for Cedar Ridge Mechanical. We are a plumbing & HVAC construction company, operating on the West Coast of Canada and USA. Logo attached.
Industry/Entity Type
Construction - Plumbing & HVAC
Contact Information for Business Card
Name, address, phone numbers, email, website address
Look and feel
Each slider illustrates characteristics of the customer's brand and the style your logo design should communicate.

```html
<!DOCTYPE html>
<html lang="en">
<head>
<meta charset="utf-8">
<title>Cedar Ridge Mechanical – Business Card</title>
<link href="https://fonts.googleapis.com/css2?family=Oswald:wght@500;700&family=Roboto:wght@400&display=swap" rel="stylesheet">
<style>
  :root {
    --backdrop: #c9c9c9;
    --ink: #000000;
    --paper: #ffffff;
    --ghost-dark: #1b1b1b;
    --ghost-light: #ececec;
    --text: #111111;
  }
  * { margin: 0; padding: 0; box-sizing: border-box; }
  html, body { width: 1200px; height: 900px; overflow: hidden; }
  body {
    background: var(--backdrop);
    font-family: "Roboto", sans-serif;
    position: relative;
  }
  .card {
    position: absolute;
    left: 260px;
    width: 680px;
    height: 388px;
    border-radius: 34px;
    overflow: hidden;
  }
  .card--front { top: 48px; background: var(--ink); }
  .card--back { top: 464px; background: var(--paper); }

  .brand-name {
    font-family: "Oswald", sans-serif;
    font-weight: 700;
    text-transform: uppercase;
    letter-spacing: 2px;
    white-space: nowrap;
    position: absolute;
  }
  .brand-mark {
    position: absolute;
    width: 40px;
    height: 40px;
    border: 7px solid currentColor;
  }

  /* front */
  .card--front .ghost {
    position: absolute;
    left: 500px;
    top: 232px;
    width: 200px;
    height: 200px;
    border: 24px solid var(--ghost-dark);
    border-radius: 22px;
  }
  .card--front .brand { color: var(--paper); }
  .card--front .brand-mark { left: 110px; top: 172px; }
  .card--front .brand-name { left: 168px; top: 168px; font-size: 38px; line-height: 48px; }

  /* back */
  .card--back .ghost {
    position: absolute;
    left: 470px;
    top: 96px;
    width: 180px;
    height: 180px;
    border: 22px solid var(--ghost-light);
    border-radius: 20px;
  }
  .card--back .brand { color: var(--ink); }
  .card--back .brand-mark { left: 50px; top: 48px; }
  .card--back .brand-name { left: 106px; top: 44px; font-size: 30px; line-height: 48px; }

  .holder { position: absolute; left: 50px; top: 170px; }
  .holder__accent {
    position: absolute; left: -50px; top: 4px;
    width: 12px; height: 56px; background: var(--ink);
  }
  .holder__name {
    font-family: "Oswald", sans-serif;
    font-weight: 700;
    font-size: 32px;
    line-height: 38px;
    text-transform: uppercase;
    color: var(--text);
  }
  .holder__role { font-size: 19px; color: var(--text); line-height: 24px; }

  .contact-list { position: absolute; left: 50px; top: 262px; list-style: none; }
  .contact-list li {
    display: flex; align-items: center; gap: 12px;
    font-size: 19px; line-height: 31px; color: var(--text);
  }
  .contact-list svg { width: 18px; height: 18px; flex: none; }

  .address {
    position: absolute; right: 40px; top: 296px;
    text-align: right; font-size: 19px; line-height: 26px; color: var(--text);
    font-style: normal;
  }
</style>
</head>
<body>
  <section class="card card--front" aria-label="Business card front">
    <div class="ghost" aria-hidden="true"></div>
    <div class="brand">
      <span class="brand-mark"></span>
      <span class="brand-name">Cedar Ridge Mechanical</span>
    </div>
  </section>

  <section class="card card--back" aria-label="Business card back">
    <div class="ghost" aria-hidden="true"></div>
    <div class="brand">
      <span class="brand-mark"></span>
      <span class="brand-name">Cedar Ridge Mechanical</span>
    </div>

    <div class="holder">
      <span class="holder__accent"></span>
      <p class="holder__name">Daniel Carter</p>
      <p class="holder__role">Managing Director</p>
    </div>

    <ul class="contact-list">
      <li>
        <svg viewBox="0 0 24 24" aria-hidden="true"><path fill="#111" d="M6.6 10.8a15.1 15.1 0 0 0 6.6 6.6l2.2-2.2c.3-.3.7-.4 1-.2 1.1.4 2.3.6 3.6.6.6 0 1 .4 1 1V20c0 .6-.4 1-1 1A17 17 0 0 1 3 4c0-.6.4-1 1-1h3.5c.6 0 1 .4 1 1 0 1.3.2 2.5.6 3.6.1.3 0 .7-.2 1z"/></svg>
        044-987 654 321
      </li>
      <li>
        <svg viewBox="0 0 24 24" aria-hidden="true"><rect x="2" y="5" width="20" height="14" rx="1" fill="#111"/><path d="M2 6l10 7 10-7" stroke="#fff" stroke-width="1.6" fill="none"/></svg>
        info@cedarridgemech.com
      </li>
      <li>
        <svg viewBox="0 0 24 24" aria-hidden="true"><circle cx="12" cy="12" r="9.5" fill="none" stroke="#111" stroke-width="2"/><ellipse cx="12" cy="12" rx="4" ry="9.5" fill="none" stroke="#111" stroke-width="1.6"/><path d="M2.5 12h19M4 7h16M4 17h16" stroke="#111" stroke-width="1.4"/></svg>
        www.cedarridgemech.com
      </li>
    </ul>

    <address class="address">
      118, Harbour View Road<br>V7M 1A3, Canada
    </address>
  </section>
</body>
</html>
```